Modern business card design for professional copywriter

I'd like a business card design that I can use to have my cards printed out by quillprint.com as a squared corners business card (see artwork and design guidelines here: https://help.quillprint.com/hc/en-gb/sections/200570950-QUILL-Product-Templates)

The design should be clean and modern and reflect the colours, tone and branding on my website: https://tessavorrin.com.au

Target Market(s)

Professionals, B2B small business owners

Industry/Entity Type

Business

Contact Information for Business Card

Tessa Vorrin
m: 0468 905 327
e: tessa@tessavorrin.com.au
w: tessavorrin.com.au

Font styles to use
Sans Serif

Requirements
Must have
• Tagline: "Clear copywriting for busy business owners"
• Brand colours: fd8000, 009984, 666666 and black
Nice to have

```html
<!DOCTYPE html>
<html lang="en">
<head>
<meta charset="utf-8">
<title>Tessa Vorrin – Business Card</title>
<link href="https://fonts.googleapis.com/css2?family=Montserrat:wght@400;500;600&display=swap" rel="stylesheet">
<style>
  :root {
    --orange: #f07f1d;
    --teal: #0f9683;
    --grey-bg: #a6a7ab;
    --card: #ffffff;
    --shadow: rgba(40, 40, 45, 0.55);
  }
  html, body {
    margin: 0;
    padding: 0;
    width: 1200px;
    height: 940px;
    overflow: hidden;
    background: var(--grey-bg);
    font-family: "Montserrat", sans-serif;
  }
  .stage {
    position: relative;
    width: 1200px;
    height: 940px;
  }
  .card {
    position: absolute;
    left: 252px;
    width: 684px;
    height: 390px;
    background: var(--card);
    border-radius: 14px;
    box-shadow: 6px 8px 8px var(--shadow);
  }
  .card--front { top: 50px; }
  .card--back  { top: 486px; }

  .brand {
    position: absolute;
    display: flex;
    align-items: center;
    gap: 10px;
    color: var(--orange);
    font-weight: 500;
    font-size: 29px;
    letter-spacing: -0.3px;
    white-space: nowrap;
  }
  .brand__dot {
    width: 14px;
    height: 14px;
    border-radius: 50%;
    background: var(--teal);
  }
  .card--front .brand { right: 40px; top: 96px; }
  .card--back .brand { left: 50%; top: 166px; transform: translateX(-50%); }

  .holder-name {
    position: absolute;
    left: 53px;
    top: 226px;
    margin: 0;
    color: var(--orange);
    font-weight: 600;
    font-size: 30px;
  }
  .divider {
    position: absolute;
    left: 53px;
    top: 279px;
    width: 581px;
    height: 2px;
    background: var(--teal);
  }
  .contact {
    position: absolute;
    left: 53px;
    top: 296px;
    margin: 0;
    padding: 0;
    list-style: none;
  }
  .contact__item {
    display: flex;
    align-items: center;
    height: 22.5px;
    font-size: 18px;
    font-weight: 400;
  }
  .contact__icon {
    width: 17px;
    height: 17px;
    margin-right: 16px;
    flex: none;
  }
  .contact__item--phone { color: var(--orange); }
  .contact__item--email { color: var(--teal); }
  .contact__item--web   { color: var(--orange); }

  .tagline {
    position: absolute;
    left: 0;
    right: 0;
    top: 236px;
    margin: 0;
    text-align: center;
    color: var(--orange);
    font-size: 19px;
    font-weight: 400;
    letter-spacing: 0.2px;
    white-space: nowrap;
  }
</style>
</head>
<body>
<main class="stage">

  <section class="card card--front" aria-label="Card front">
    <div class="brand"><span class="brand__dot"></span>Tessa Vorrin</div>

    <h1 class="holder-name">Tessa Vorrin</h1>
    <div class="divider"></div>

    <ul class="contact">
      <li class="contact__item contact__item--phone">
        <svg class="contact__icon" viewBox="0 0 17 17" aria-hidden="true">
          <circle cx="8.5" cy="8.5" r="8.5" fill="#0f9683"/>
          <rect x="5.5" y="3.5" width="6" height="10" rx="1" fill="#fff"/>
          <rect x="6.5" y="4.8" width="4" height="6.5" fill="#0f9683"/>
        </svg>
        0468 905 327
      </li>
      <li class="contact__item contact__item--email">
        <svg class="contact__icon" viewBox="0 0 17 17" aria-hidden="true">
          <circle cx="8.5" cy="8.5" r="8.5" fill="#0f9683"/>
          <rect x="4" y="5.5" width="9" height="6" rx="0.8" fill="#fff"/>
          <path d="M4.4 6 L8.5 9 L12.6 6" fill="none" stroke="#0f9683" stroke-width="1"/>
        </svg>
        tessa@tessavorrin.com.au
      </li>
      <li class="contact__item contact__item--web">
        <svg class="contact__icon" viewBox="0 0 17 17" aria-hidden="true">
          <circle cx="8.5" cy="8.5" r="8.5" fill="#0f9683"/>
          <g fill="none" stroke="#fff" stroke-width="0.9">
            <circle cx="8.5" cy="8.5" r="5"/>
            <ellipse cx="8.5" cy="8.5" rx="2.2" ry="5"/>
            <line x1="3.5" y1="8.5" x2="13.5" y2="8.5"/>
            <line x1="4.3" y1="6" x2="12.7" y2="6"/>
            <line x1="4.3" y1="11" x2="12.7" y2="11"/>
          </g>
        </svg>
        tessavorrin.com.au
      </li>
    </ul>
  </section>

  <section class="card card--back" aria-label="Card back">
    <div class="brand"><span class="brand__dot"></span>Tessa Vorrin</div>
    <p class="tagline">"Clear copywriting for busy business owners"</p>
  </section>

</main>
</body>
</html>
```